Business Cards for new orthopaedic surgery practice

My husband and I are starting our own orthopaedic surgery practice. We are looking for a business card that is uniform, but one will have my name/title and the other will have his. You can just create one design with my name on it for now. But when I choose your design as the winning design I will ask that you add another copy with his name/title.

We are looking for classy, simple, elite all in one. We like dark blues/a little gold/yellow. Something that goes with our logo. We want our logo incorporated. Here is all the info you need:
Business name: RV Bone & Vitality Center
Location: 38517 North Willowmere Ave
Palm Meadows, FL 33498
Phone: 954-218-4063
Fax: 954-582-7341
Email: info@myrvbonecare.example

Names: Lydia Vance, M.D.
Board Certified Hand and Upper Extremity Surgeon

Ebo Dansu, M.D.
Board Certified Hip & Knee Replacement/General Orthopaedic Surgeon

Can decide what you want to put on the back. Maybe a slogan:
Rooted in Care. Focused on You

I am just going to upload our logo. The only thing is if we select you as the winning design, the location, and phone numbers may change. We will need your help to update that once fully solidified.

Industry/Entity Type

Medical

Contact Information for Business Card

Colors
0054AA
0677BA
7BADD7
CADEEF
E8F1F8
0094D4
00A9DD
6FCCEA
C7EBF8
E9F6FB

Requirements
Must have
• class, appeal,
Should not have
• We want to air on the side of masculine if we are looking at masculine vs. feminine feel. But we still want it classy, sophisticated, and something we will love

```html
<!DOCTYPE html>
<html lang="en">
<head>
<meta charset="utf-8">
<title>RV Bone &amp; Vitality Center – Business Card</title>
<link rel="stylesheet" href="https://fonts.googleapis.com/css2?family=Poppins:wght@400;500&family=Roboto:wght@500&display=swap">
<style>
  :root {
    --navy: #1b2a4e;
    --gold: #c8a360;
    --white: #ffffff;
    --backdrop: #e2e8ea;
  }
  * { margin: 0; padding: 0; box-sizing: border-box; }
  html, body { width: 1200px; height: 960px; overflow: hidden; }
  body { background: var(--backdrop); font-family: "Poppins", sans-serif; position: relative; }

  .card { position: absolute; left: 248px; width: 704px; height: 402px; overflow: hidden; }
  .card-front { top: 58px; background: var(--navy); }
  .card-back { top: 500px; background: var(--white); }

  .brand-ring {
    position: absolute; border-radius: 50%;
    display: flex; align-items: center; justify-content: center; text-align: center;
    font-family: "Poppins", sans-serif; font-weight: 500; letter-spacing: 0.04em; line-height: 1.35;
  }
  .card-front .brand-ring {
    left: 248px; top: 87px; width: 204px; height: 204px;
    border: 2px solid var(--white); color: var(--white); font-size: 19px;
  }
  .slogan {
    position: absolute; left: 0; right: 0; top: 356px; text-align: center;
    color: var(--white); font-size: 14px; letter-spacing: 0.04em;
  }
  .slogan .dot {
    display: inline-block; width: 7px; height: 7px; border-radius: 50%;
    background: var(--white); margin: 0 6px 2px 0; vertical-align: middle;
  }
  .slogan .gap { margin-left: 8px; }

  .card-back .brand-ring {
    left: 27px; top: 31px; width: 142px; height: 142px;
    border: 2px solid var(--gold); color: var(--navy); font-size: 14px;
  }
  .doctor { position: absolute; right: 27px; top: 30px; text-align: right; }
  .doctor-name {
    font-family: "Roboto", sans-serif; font-weight: 500; color: var(--gold);
    font-size: 22px; letter-spacing: 0.03em; line-height: 1.1;
  }
  .doctor-title { color: var(--navy); font-size: 15px; letter-spacing: 0.03em; margin-top: 8px; }
  .accent-bar { position: absolute; left: 684px; top: 32px; width: 20px; height: 53px; background: var(--gold); }

  .address {
    position: absolute; left: 26px; top: 212px; color: var(--gold);
    font-size: 17.5px; line-height: 24.5px; letter-spacing: 0.03em;
  }
  .contact-band { position: absolute; left: 0; top: 269px; width: 572px; height: 133px; background: var(--gold); }
  .contact-list { position: absolute; left: 26px; top: 279px; list-style: none; }
  .contact-list li {
    display: flex; align-items: center; height: 24.5px;
    color: var(--white); font-size: 17.5px; letter-spacing: 0.03em;
  }
  .contact-list svg { width: 16px; height: 16px; margin-right: 11px; flex: none; }

  .brand-corner {
    position: absolute; left: 584px; top: 300px; width: 112px;
    color: var(--navy); font-weight: 500; font-size: 18px; line-height: 1.3; text-align: center;
  }
</style>
</head>
<body>
  <section class="card card-front">
    <div class="brand-ring">RV Bone &amp;<br>Vitality<br>Center</div>
    <p class="slogan"><span class="dot"></span>Rooted in Care <span class="dot gap"></span>Focused on You</p>
  </section>

  <section class="card card-back">
    <div class="brand-ring">RV Bone &amp;<br>Vitality<br>Center</div>

    <div class="doctor">
      <p class="doctor-name">Lydia Vance, M.D.</p>
      <p class="doctor-title">Hand and Upper Extremity Surgery</p>
    </div>
    <div class="accent-bar"></div>

    <p class="address">38517 North Willowmere Ave<br>Palm Meadows, FL 33498</p>

    <div class="contact-band"></div>
    <ul class="contact-list">
      <li>
        <svg viewBox="0 0 16 16" fill="none" stroke="#fff" stroke-width="1.4" stroke-linecap="round"><path d="M3 2l3 .5 1 3-1.8 1.3a9 9 0 0 0 4 4L10.5 9l3 1 .5 3c-1 1-2 1.5-3 1.3C6.5 13.5 2.5 9.5 1.7 5 1.5 4 2 3 3 2z"/><path d="M10 2.5a4 4 0 0 1 3.5 3.5M10 5a1.5 1.5 0 0 1 1 1"/></svg>
        954-218-4063
      </li>
      <li>
        <svg viewBox="0 0 16 16" fill="none" stroke="#fff" stroke-width="1.4"><rect x="1.5" y="5" width="4" height="9.5"/><rect x="5.5" y="6.5" width="9" height="8"/><path d="M7.5 6.5V1.5h5v5"/><path d="M8 9h1M10.5 9h1M8 11.5h1M10.5 11.5h1"/></svg>
        954-582-7341
      </li>
      <li>
        <svg viewBox="0 0 16 16" fill="none" stroke="#fff" stroke-width="1.3"><circle cx="8" cy="8" r="6.5"/><ellipse cx="8" cy="8" rx="3" ry="6.5"/><path d="M1.5 8h13M2.5 4.8h11M2.5 11.2h11"/></svg>
        www.myrvbonecare.example
      </li>
      <li>
        <svg viewBox="0 0 16 16" fill="none" stroke="#fff" stroke-width="1.3" stroke-linejoin="round"><path d="M1.5 6.5L8 2l6.5 4.5v8h-13z"/><path d="M1.5 6.5L8 11l6.5-4.5"/><circle cx="8" cy="6.5" r="1.6"/></svg>
        info@myrvbonecare.example
      </li>
    </ul>

    <div class="brand-corner">RV Bone &amp; Vitality Center</div>
  </section>
</body>
</html>
```